Request for Business Card Design

Hi. My name is Marlene, I am looking for a new business card design for my company, Quarrow Signal Instruments, LLC. I really like the design you did for Tarsel Venture and was hoping you could do something similar using our full logo and our mark. I am also open to any raised texture design using our mark. I have attached our full logo, which would need to be somewhere on the card, as well as the mark in both outline and full form, as well as our brand colors / guide. The card does not have to be white, as long as our logo and mark appear. I actually like darker colored business cards more, but am open to all options. If you are interested in working with me, please let me know. We would also take the business card design into letterhead design if you can do that.

```html
<!DOCTYPE html>
<html lang="en">
<head>
<meta charset="utf-8">
<title>Quarrow Signal Instruments — Business Cards</title>
<link rel="stylesheet" href="https://fonts.googleapis.com/css2?family=Open+Sans:wght@400;600;700;800&display=swap">
<style>
  :root {
    --stage: #232323;
    --card-dark: #3a3a3c;
    --card-dark-deep: #2c2c2e;
    --brand-blue: #1a9cca;
    --brand-blue-deep: #0f86ad;
    --text-light: #f2f2f2;
    --text-muted: #d6d6d6;
  }
  * { box-sizing: border-box; margin: 0; padding: 0; }
  html, body {
    width: 1200px; height: 780px; overflow: hidden;
    background: var(--stage);
    font-family: "Open Sans", Arial, sans-serif;
  }
  .sheet {
    position: relative; width: 1200px; height: 780px;
    display: flex; align-items: center; justify-content: center; gap: 50px;
  }
  .card {
    position: relative; width: 530px; height: 303px;
    border-radius: 3px; overflow: hidden;
    box-shadow: 0 14px 30px rgba(0,0,0,.45);
  }

  /* Front */
  .card-front { background: var(--card-dark); color: var(--text-light); }
  .front-wordmark {
    position: absolute; left: 34px; top: 28px;
    display: flex; align-items: center; gap: 12px;
  }
  .wordmark-dot {
    width: 34px; height: 34px; border-radius: 50%;
    background: var(--brand-blue);
  }
  .wordmark-name {
    font-weight: 800; font-size: 30px; letter-spacing: 3px; line-height: 1;
    color: var(--text-light);
  }
  .wordmark-tag {
    font-weight: 800; font-size: 9.5px; letter-spacing: 1.4px;
    color: var(--text-light); margin-top: 4px;
  }
  .contact {
    position: absolute; left: 34px; top: 104px;
  }
  .contact-name {
    font-weight: 700; font-size: 30px; line-height: 1.05; color: var(--brand-blue);
  }
  .contact-role { font-size: 13px; margin-top: 2px; color: var(--text-light); }
  .contact-address { font-size: 12.5px; line-height: 1.45; margin-top: 8px; color: var(--text-light); }
  .contact-lines { list-style: none; margin-top: 8px; }
  .contact-lines li {
    display: flex; align-items: center; gap: 8px;
    font-size: 12.5px; line-height: 1.5; color: var(--text-light);
  }
  .contact-lines svg { width: 11px; height: 11px; flex: none; }
  .emboss-area {
    position: absolute; right: 18px; bottom: 14px; width: 220px; height: 240px;
    border-radius: 110px 110px 24px 24px;
    background: radial-gradient(circle at 60% 40%, #4a4a4c 0%, var(--card-dark-deep) 70%);
  }

  /* Back */
  .card-back { background: var(--brand-blue); }
  .pattern-area {
    position: absolute; inset: 0;
    background: linear-gradient(115deg, var(--brand-blue-deep) 0%, var(--brand-blue) 55%, #5cbfe0 100%);
  }
  .back-wordmark {
    position: absolute; left: 50%; bottom: 30px; transform: translateX(-50%);
    display: flex; align-items: center; gap: 8px;
  }
  .back-wordmark .wordmark-dot { width: 18px; height: 18px; background: #ffffff; }
  .back-wordmark .wordmark-name { font-size: 16px; letter-spacing: 2px; color: #ffffff; }
  .back-wordmark .wordmark-tag { font-size: 5.5px; letter-spacing: .8px; margin-top: 2px; color: #ffffff; }
</style>
</head>
<body>
<main class="sheet">

  <section class="card card-front" aria-label="Business card front">
    <div class="front-wordmark">
      <span class="wordmark-dot" aria-hidden="true"></span>
      <div>
        <div class="wordmark-name">QUARROW</div>
        <div class="wordmark-tag">SIGNAL INSTRUMENTS</div>
      </div>
    </div>

    <div class="contact">
      <h1 class="contact-name">Marlene</h1>
      <p class="contact-role">Director</p>
      <p class="contact-address">1180 Fenwick Row •<br>Aldmere, CO 80619</p>
      <ul class="contact-lines">
        <li>
          <svg viewBox="0 0 12 12" aria-hidden="true"><path fill="#1a9cca" d="M2.5 1l2 2.2-1 1.3a7 7 0 0 0 4 4l1.3-1 2.2 2-1.2 1.5C5.5 11 1 6.5 1 2.2z"/></svg>
          +001 555 210 4837
        </li>
        <li>
          <svg viewBox="0 0 12 12" aria-hidden="true"><rect x="1" y="3" width="10" height="7" rx="1" fill="#1a9cca"/><rect x="3" y="1" width="6" height="3" fill="#1a9cca"/></svg>
          +001 555 210 4902
        </li>
        <li>
          <svg viewBox="0 0 12 12" aria-hidden="true"><circle cx="6" cy="6" r="5" fill="none" stroke="#1a9cca" stroke-width="1.4"/><path d="M1 6h10M6 1c-2.5 3-2.5 7 0 10M6 1c2.5 3 2.5 7 0 10" fill="none" stroke="#1a9cca" stroke-width="1"/></svg>
          www.quarrowsignal.com
        </li>
        <li>
          <svg viewBox="0 0 12 12" aria-hidden="true"><rect x="1" y="2.5" width="10" height="7" rx="1" fill="#1a9cca"/><path d="M1.5 3l4.5 3.5L10.5 3" fill="none" stroke="#3a3a3c" stroke-width="1"/></svg>
          info@quarrowsignal.com
        </li>
      </ul>
    </div>

    <div class="emboss-area" role="img" aria-label="Large raised brand mark embossed in dark tone"></div>
  </section>

  <section class="card card-back" aria-label="Business card back">
    <div class="pattern-area" role="img" aria-label="Repeating brand mark pattern fading to light blue"></div>
    <div class="back-wordmark">
      <span class="wordmark-dot" aria-hidden="true"></span>
      <div>
        <div class="wordmark-name">QUARROW</div>
        <div class="wordmark-tag">SIGNAL INSTRUMENTS</div>
      </div>
    </div>
  </section>

</main>
</body>
</html>
```